NimbaVault Website Homepage Design

Please provide your idea of homepage for a hosting company. This project is for DESIGN only, no coding.

It must use/combine colors used in logo, clean, modern look.

Homepage must consist of at least 4 sections (example: testimonials, services, and so on. not necesarily all of them). We would like the navigation to be horizontal, but not mandatory.

You can include a preview of services page (optional, not a must).

Number of Pages Required

1 page

Font styles to use
Sans Serif

```html
<!DOCTYPE html>
<html lang="en">
<head>
<meta charset="UTF-8">
<title>NimbaVault – Hosting Homepage</title>
<link href="https://fonts.googleapis.com/css2?family=Montserrat:wght@400;500;600;700;800&family=Open+Sans:wght@400;600&display=swap" rel="stylesheet">
<style>
  :root{
    --blue:#1e8be6;
    --blue-light:#4fb0f5;
    --blue-deep:#0f5fc4;
    --navy:#0c1b5a;
    --ink:#1c1c1c;
    --grey:#7a7f88;
    --line:#e4e8ee;
    --white:#ffffff;
    --footer:#151515;
    --footer-text:#c9c9c9;
    --card1:#0c1b5a;
    --card2:#13288c;
    --card3:#1b43b8;
    --card4:#2f64d8;
    --card5:#6794f2;
  }
  *{box-sizing:border-box;margin:0;padding:0}
  html,body{width:1200px;height:2440px;overflow:hidden;background:var(--white)}
  body{font-family:"Open Sans",Arial,sans-serif;color:var(--ink);position:relative}
  h1,h2,h3,.brand,.nav a,.btn{font-family:"Montserrat",Arial,sans-serif}

  /* header */
  .site-header{position:absolute;top:0;left:0;width:1200px;height:64px;display:flex;align-items:center;justify-content:space-between;padding:0 90px 0 96px;background:var(--white);z-index:3}
  .brand{font-weight:800;font-size:30px;letter-spacing:1px;color:var(--blue)}
  .nav{display:flex;gap:34px;align-items:center}
  .nav a{font-size:14px;color:#333;text-decoration:none;font-weight:500}
  .nav a.active{border-bottom:2px solid var(--blue);padding-bottom:3px}

  /* hero */
  .hero{position:absolute;top:64px;left:0;width:1200px;height:520px;background:linear-gradient(120deg,#1a7fe0 0%,#2f9af0 55%,#6cc4fb 100%);overflow:hidden}
  .hero-copy{position:absolute;left:96px;top:110px;width:480px;color:var(--white)}
  .hero-copy h1{font-size:58px;font-weight:500;letter-spacing:2px;line-height:1}
  .hero-copy p{font-size:16px;line-height:1.45;margin-top:20px}
  .hero-copy h3{font-size:22px;font-weight:500;margin-top:22px;letter-spacing:.5px}
  .btn{display:inline-flex;align-items:center;gap:8px;border-radius:30px;font-size:14px;font-weight:600;padding:0 32px;height:52px}
  .btn-light{background:var(--white);color:var(--blue);margin-top:30px}
  .btn-blue{background:var(--blue);color:var(--white)}
  .hero-art{position:absolute;left:650px;top:30px;width:480px;height:390px;border-radius:24px;background:radial-gradient(circle at 50% 55%,#e9f4ff 0%,#9fd0fa 55%,rgba(110,190,250,0) 75%)}
  .hero-wave{position:absolute;left:0;bottom:0}

  /* about */
  .about{position:absolute;top:640px;left:0;width:1200px;height:520px}
  .about-art{position:absolute;left:80px;top:20px;width:440px;height:420px;border-radius:24px;background:radial-gradient(circle at 50% 50%,#dbeefe 0%,#b4dafa 50%,rgba(255,255,255,0) 75%)}
  .about-copy{position:absolute;left:596px;top:90px;width:520px}
  .about-copy h2{font-size:44px;font-weight:700;letter-spacing:1px}
  .about-copy .lead{color:var(--blue);font-weight:600;font-size:14px;line-height:1.55;margin-top:18px}
  .about-copy .body{color:var(--grey);font-size:13px;line-height:1.7;margin-top:14px}
  .about-copy .btn{margin:30px 0 0 0}

  /* services */
  .section-title{position:absolute;left:0;width:1200px;text-align:center;font-family:"Montserrat",Arial,sans-serif;font-size:44px;font-weight:700;letter-spacing:1px}
  .services{position:absolute;top:1280px;left:100px;width:1000px;height:240px;display:flex}
  .service{flex:1;height:240px;color:var(--white);padding:26px 20px;position:relative}
  .service:nth-child(1){background:var(--card1)}
  .service:nth-child(2){background:var(--card2)}
  .service:nth-child(3){background:var(--card3)}
  .service:nth-child(4){background:var(--card4)}
  .service:nth-child(5){background:var(--card5)}
  .service svg{display:block}
  .service small{display:block;font-size:10px;letter-spacing:1px;margin-top:62px}
  .service h3{font-size:17px;font-weight:600;line-height:1.25;margin-top:14px}

  /* testimonials */
  .testimonials{position:absolute;top:1680px;left:90px;width:1020px;display:flex;gap:28px}
  .quote{flex:1;height:196px;background:var(--white);box-shadow:0 3px 14px rgba(0,0,0,.12);padding:26px 26px}
  .quote-head{display:flex;align-items:center;gap:18px}
  .avatar{width:62px;height:62px;border-radius:50%;background:linear-gradient(135deg,#c9a98c,#7d5f4a)}
  .quote-head h3{font-size:18px;font-weight:600}
  .quote-head span{font-size:11px;color:var(--grey)}
  .quote p{font-size:12px;color:var(--grey);line-height:1.6;margin-top:16px}
  .dots{position:absolute;top:1900px;left:0;width:1200px;display:flex;justify-content:center;gap:8px}
  .dots i{width:22px;height:3px;background:#c8ccd3}
  .dots i.on{background:var(--blue)}

  /* footer */
  .site-footer{position:absolute;top:1960px;left:0;width:1200px;height:480px}
  .site-footer svg{position:absolute;top:0;left:0}
  .footer-brand{position:absolute;left:96px;top:186px;font-size:44px}
  .footer-col{position:absolute;top:180px;color:var(--white)}
  .footer-col h3{font-size:18px;font-weight:600;margin-bottom:20px}
  .footer-col li{list-style:none;font-size:12px;color:var(--footer-text);line-height:1.9}
  .copyright{position:absolute;left:0;bottom:36px;width:1200px;text-align:center;font-size:11px;color:var(--footer-text)}
</style>
</head>
<body>

<header class="site-header">
  <div class="brand">NIMBAVAULT</div>
  <nav class="nav">
    <a class="active">Home</a><a>About Us</a><a>Services</a><a>Blog</a><a>Contact Us</a>
    <svg width="16" height="16" viewBox="0 0 16 16" aria-label="Search"><circle cx="6.5" cy="6.5" r="5" fill="none" stroke="#333" stroke-width="2"/><line x1="10.5" y1="10.5" x2="15" y2="15" stroke="#333" stroke-width="2"/></svg>
  </nav>
</header>

<section class="hero">
  <div class="hero-copy">
    <h1>NIMBAVAULT</h1>
    <p>Lorem ipsum dolor sit amet, consectetur adipiscing elit, sed do eiusmod tempor incididunt ut labore et dolore magna aliqua.</p>
    <h3>LOREM IPSUM DOLOR SIT AMET</h3>
    <span class="btn btn-light">Get Started
      <svg width="14" height="14" viewBox="0 0 14 14"><circle cx="7" cy="7" r="7" fill="#1e8be6"/><path d="M5.5 4l3 3-3 3" stroke="#fff" stroke-width="1.6" fill="none"/></svg>
    </span>
  </div>
  <div class="hero-art" role="img" aria-label="Isometric illustration of a laptop beside cloud server racks and small figures"></div>
  <svg class="hero-wave" width="1200" height="110" viewBox="0 0 1200 110">
    <path d="M0 60 C200 20 380 100 600 70 C820 40 980 90 1200 50 L1200 110 L0 110Z" fill="#a9dcfb" opacity=".6"/>
    <path d="M0 85 C240 50 420 110 640 88 C860 66 1000 105 1200 80 L1200 110 L0 110Z" fill="#ffffff"/>
  </svg>
</section>

<section class="about">
  <div class="about-art" role="img" aria-label="Isometric illustration of cloud hosting with screens and server units"></div>
  <div class="about-copy">
    <h2>ABOUT US</h2>
    <p class="lead">Lorem ipsum dolor sit amet, consectetur adipiscing elit, sed do eiusmod tempor incididunt ut labore et dolore magna aliqua.</p>
    <p class="body">Lorem ipsum dolor sit amet, consectetur adipiscing elit, sed do eiusmod tempor incididunt ut labore et dolore magna aliqua. Ut enim ad minim veniam, quis nostrud exercitation ullamco laboris nisi ut aliquip ex ea commodo consequat. Duis aute irure dolor in reprehenderit in voluptate velit esse cillum dolore eu fugiat nulla pariatur. Excepteur sint occaecat cupidatat non proident, sunt in culpa qui officia deserunt mollit anim id est laborum.</p>
    <span class="btn btn-blue">Read More
      <svg width="14" height="14" viewBox="0 0 14 14"><circle cx="7" cy="7" r="7" fill="#fff"/><path d="M5.5 4l3 3-3 3" stroke="#1e8be6" stroke-width="1.6" fill="none"/></svg>
    </span>
  </div>
</section>

<h2 class="section-title" style="top:1206px">OUR SERVICES</h2>
<section class="services">
  <article class="service">
    <svg width="34" height="34" viewBox="0 0 34 34" fill="none" stroke="#fff" stroke-width="1.6"><rect x="3" y="5" width="28" height="18" rx="2"/><line x1="12" y1="29" x2="22" y2="29"/><line x1="17" y1="23" x2="17" y2="29"/></svg>
    <small>LOREM IPSUM</small><h3>Web<br>hosting</h3>
  </article>
  <article class="service">
    <svg width="34" height="34" viewBox="0 0 34 34" fill="none" stroke="#fff" stroke-width="1.6"><rect x="4" y="4" width="26" height="26" rx="2"/><line x1="4" y1="11" x2="30" y2="11"/><line x1="9" y1="17" x2="25" y2="17"/><line x1="9" y1="23" x2="20" y2="23"/></svg>
    <small>LOREM IPSUM</small><h3>Wordpress<br>hosting</h3>
  </article>
  <article class="service">
    <svg width="34" height="34" viewBox="0 0 34 34" fill="none" stroke="#fff" stroke-width="1.6"><path d="M9 24a6 6 0 0 1 1-12 8 8 0 0 1 15 2 5 5 0 0 1 0 10z"/></svg>
    <small>LOREM IPSUM</small><h3>Cloud<br>hosting</h3>
  </article>
  <article class="service">
    <svg width="34" height="34" viewBox="0 0 34 34" fill="none" stroke="#fff" stroke-width="1.6"><rect x="5" y="4" width="24" height="8" rx="1"/><rect x="5" y="14" width="24" height="8" rx="1"/><rect x="5" y="24" width="24" height="7" rx="1"/><circle cx="10" cy="8" r="1"/><circle cx="10" cy="18" r="1"/></svg>
    <small>LOREM IPSUM</small><h3>Dedicated<br>server</h3>
  </article>
  <article class="service">
    <svg width="34" height="34" viewBox="0 0 34 34" fill="none" stroke="#fff" stroke-width="1.6"><rect x="4" y="6" width="26" height="20" rx="2"/><line x1="4" y1="12" x2="30" y2="12"/><path d="M12 18l3 3 6-6"/></svg>
    <small>LOREM IPSUM</small><h3>VPS</h3>
  </article>
</section>

<h2 class="section-title" style="top:1606px">TESTIMONIALS</h2>
<section class="testimonials">
  <article class="quote">
    <div class="quote-head"><div class="avatar" role="img" aria-label="Customer portrait"></div><div><h3>Lena Marsh</h3><span>Lorem ipsum dolor</span></div></div>
    <p>Lorem ipsum dolor sit amet, consectetur adipiscing elit, sed do eiusmod tempor incididunt ut labore et dolore magna aliqua.</p>
  </article>
  <article class="quote">
    <div class="quote-head"><div class="avatar" role="img" aria-label="Customer portrait"></div><div><h3>Lena Marsh</h3><span>Lorem ipsum dolor</span></div></div>
    <p>Lorem ipsum dolor sit amet, consectetur adipiscing elit, sed do eiusmod tempor incididunt ut labore et dolore magna aliqua.</p>
  </article>
  <article class="quote">
    <div class="quote-head"><div class="avatar" role="img" aria-label="Customer portrait"></div><div><h3>Lena Marsh</h3><span>Lorem ipsum dolor</span></div></div>
    <p>Lorem ipsum dolor sit amet, consectetur adipiscing elit, sed do eiusmod tempor incididunt ut labore et dolore magna aliqua.</p>
  </article>
</section>
<div class="dots"><i class="on"></i><i></i><i></i></div>

<footer class="site-footer">
  <svg width="1200" height="480" viewBox="0 0 1200 480">
    <path d="M0 70 C180 10 360 110 600 60 C820 15 1000 100 1200 40 L1200 480 L0 480Z" fill="#3a3a3a"/>
    <path d="M0 100 C220 40 400 130 620 90 C840 50 1010 120 1200 75 L1200 480 L0 480Z" fill="var(--footer)"/>
  </svg>
  <div class="brand footer-brand">NIMBAVAULT</div>
  <div class="footer-col" style="left:570px"><h3>Links</h3><ul><li>Home</li><li>About Us</li><li>Services</li><li>Blog</li><li>Contact Us</li></ul></div>
  <div class="footer-col" style="left:768px"><h3>Others</h3><ul><li>FAQ</li><li>Privacy Policy</li><li>Terms &amp; Conditions</li></ul></div>
  <div class="footer-col" style="left:1010px"><h3>Follow Us</h3><ul><li>Friendloop</li><li>Pictobook</li><li>Chirpline</li></ul></div>
  <p class="copyright">© Copyright 2024 NimbaVault Hosting All Rights Reserved</p>
</footer>

</body>
</html>
```